Letterhead designs for Property Management firm

Would like to see some different letterhead/envelope designs We are a residential property management company. We would like to see designs that utilize blue/grays/black

```html
<!DOCTYPE html>
<html lang="en">
<head>
<meta charset="utf-8">
<title>Harborview Property Management – Letterhead</title>
<link href="https://fonts.googleapis.com/css2?family=Arimo:wght@400;700&display=swap" rel="stylesheet">
<style>
  :root {
    --backdrop: #2b2c2f;
    --paper: #f7f7f7;
    --brand-blue: #0b4da2;
    --ink-black: #1b1a19;
    --text-gray: #4f4f4f;
    --footer-white: #ffffff;
  }
  * { box-sizing: border-box; margin: 0; padding: 0; }
  html, body {
    width: 1200px; height: 1200px; overflow: hidden;
    background: var(--backdrop);
    font-family: "Arimo", Arial, sans-serif;
  }
  .letterhead {
    position: absolute; left: 181px; top: 7px;
    width: 838px; height: 1185px;
    background: var(--paper);
    overflow: hidden;
  }
  .header-wave { position: absolute; left: 0; top: 0; }
  .brand {
    position: absolute; left: 62px; top: 70px;
    display: flex; align-items: center; gap: 10px;
    color: var(--brand-blue); font-weight: 700;
    font-size: 19px; line-height: 1.15; letter-spacing: 0.3px;
  }
  .brand-square { width: 18px; height: 18px; background: var(--brand-blue); flex: none; }
  .letter {
    position: absolute; left: 89px; top: 268px; width: 662px;
    color: var(--text-gray); font-size: 14px; line-height: 19.7px;
  }
  .letter .date { margin-bottom: 39px; }
  .letter .recipient { margin-bottom: 19.7px; }
  .letter .name, .letter .sign-title { font-weight: 700; }
  .letter .salutation { margin-bottom: 19.7px; }
  .letter .body p { text-align: justify; margin-bottom: 19.7px; }
  .letter .closing { margin-top: 20px; }
  .signature {
    width: 180px; height: 20px; margin: 2px 0 3px;
    background: linear-gradient(90deg, rgba(30,30,30,0.25), rgba(30,30,30,0.08));
    border-radius: 10px;
  }
  .contact {
    position: absolute; left: 60px; top: 1066px;
    color: var(--text-gray); font-size: 14px; line-height: 17px;
  }
  .contact li { list-style: none; display: flex; align-items: center; gap: 6px; }
  .contact svg { width: 11px; height: 11px; fill: var(--brand-blue); }
  .footer-bar {
    position: absolute; left: 0; top: 1131px; width: 838px; height: 39px;
    background: var(--ink-black);
    border-left: 14px solid var(--brand-blue);
    color: var(--footer-white); font-size: 14px;
    display: flex; align-items: center; padding-left: 47px;
  }
  .footer-bar .firm { color: var(--brand-blue); font-weight: 700; margin-right: 4px; }
</style>
</head>
<body>
<article class="letterhead">
  <svg class="header-wave" width="838" height="190" viewBox="0 0 838 190" aria-hidden="true">
    <path d="M0,0 H838 V186 C720,110 560,40 330,24 C200,16 80,28 0,32 Z" fill="var(--brand-blue)"/>
    <path d="M0,32 C120,22 260,14 360,22 C470,30 560,55 612,86 C540,62 450,44 340,38 C220,32 100,40 0,52 Z" fill="var(--ink-black)"/>
  </svg>

  <div class="brand">
    <span class="brand-square"></span>
    <span>Harborview<br>Property Management</span>
  </div>

  <section class="letter">
    <p class="date">January 1, 2050</p>
    <div class="recipient">
      <p class="name">Daniel Reyes</p>
      <p>Managing Director</p>
      <p>Co.Street, Building/Suite</p>
      <p>City/State, Zip Code</p>
    </div>
    <p class="salutation">Dear Laura Whitfield,</p>
    <div class="body">
      <p>Lorem ipsum dolor sit amet, consectetuer adipiscing elit, sed diam nonummy nibh euismod tincidunt ut laoreet dolore magna aliquam erat volutpat. Ut wisi enim ad minim veniam, quis nostrud exerci tation ullamcorper suscipit lobortis nisl ut aliquip ex ea commodo consequat. Duis dolore te feugait nulla facilisi. Nam liber tempor cum soluta nobis eleifend option congue nihil imperdiet doming id quod mazim placerat facer possim assum. Lorem ipsum dolor sit amet, consectetuer adipiscing elit, sed diam nonummy nibh euismod tincidunt ut laoreet dolore magna aliquam erat volutpat. Ut wisi enim ad minim veniam, quis nostrud exerci tation ullamcorper suscipit lobortis nisl ut aliquip ex ea commodo consequat.</p>
      <p>Consectetuer adipiscing elit, sed diam nonummy nibh euismod tincidunt ut laoreet dolore magna aliquam erat volutpat. Ut wisi enim ad minim veniam, quis nostrud exerci tation ullamcorper suscipit lobortis nisl ut aliquip ex ea commodo consequat. Consectetuer adipiscing elit, sed diam nonummy nibh euismod tincidunt ut laoreet dolore magna aliquam erat volutpat. Ut wisi enim ad minim veniam, quis nostrud exerci tation ullamcorper suscipit lobortis nisl ut aliquip ex ea commodo consequat.</p>
      <p>Duis dolore te feugait nulla facilisi. Nam liber tempor cum soluta nobis eleifend option congue nihil imperdiet doming id quod mazim placerat facer possim assum.Duis dolore te feugait nulla facilisi. Nam liber tempor cum soluta nobis eleifend option congue nihil imperdiet doming id quod mazim placerat facer possim assum.</p>
    </div>
    <div class="closing">
      <p>Sincerely Yours,</p>
      <div class="signature" role="img" aria-label="Handwritten signature of the managing director"></div>
      <p class="sign-title">Authorized Managing Director</p>
      <p>Your Company Name</p>
    </div>
  </section>

  <ul class="contact">
    <li><svg viewBox="0 0 12 12"><path d="M2.5 1 L4.5 1 L5.3 3.6 L4 4.6 C4.7 6 6 7.3 7.4 8 L8.4 6.7 L11 7.5 V9.5 C11 10.3 10.3 11 9.5 11 C5 11 1 7 1 2.5 C1 1.7 1.7 1 2.5 1 Z"/></svg>555.010.4200</li>
    <li><svg viewBox="0 0 12 12"><path d="M1 2.5 H11 V9.5 H1 Z M2 3.5 V8.5 H10 V3.5 L6 6.5 Z" fill-rule="evenodd"/></svg>info@harborviewhomes.com</li>
    <li><svg viewBox="0 0 12 12"><circle cx="6" cy="6" r="5"/><path d="M1 6 H11 M6 1 C3.5 3.5 3.5 8.5 6 11 M6 1 C8.5 3.5 8.5 8.5 6 11" stroke="#fff" stroke-width="0.8" fill="none"/></svg>www.harborviewhomes.com</li>
  </ul>

  <footer class="footer-bar">
    <span class="firm">Harborview Property Management,</span>
    <span>Co.Street, Building/Suite 12345, City/State, Zip Code</span>
  </footer>
</article>
</body>
</html>
```